LoopVane - A ride hailing server VAR

our Brindle.co profile: https://brindle.co/517loopvane

LOOPVANE offers first world solutions to first world problems. These days, our smartphones are our cameras, our wallets and our ride home. LOOPVANE guarantees that even if your phone is lost or dies, you'll never get stranded again. Simply call or text (SMS) our toll-free number to request a ride, and choose from one of the various services you subscribe to. LOOPVANE verifies your identity through a unique pin, making it possible to request rides through your own account from a stranger's phone via text or phone call. You can also login through our website or our App, making it easier than ever to get home phoneless.

LOOPVANE is a heterogeneous ride-hailing service that allows users for request transportation from any "transportation network company," taxi, helicopter service, jet service or any transportation service company that is publicly available. LOOPVANE will allow users to connect through our site, automated phone system, App or any appropriated touch point available.

Target Market(s)

RIde Haling

Coding

Coded - Design and coding required

Number of Pages Required

4 page

Requirements
Must have
• hav
Nice to have
• e the same functionality as our competitor's site: https://hopquill.com/
Should not have
• should not be cheezy
• We need to have the registration/sign up on the main page like https://www.zarvix.com/

```html
<!DOCTYPE html>
<html lang="en">
<head>
<meta charset="utf-8">
<title>LoopVane</title>
<link href="https://fonts.googleapis.com/css2?family=Open+Sans:wght@400;600;700&display=swap" rel="stylesheet">
<style>
:root{
  --orange:#f5a000;
  --orange-light:#ffc21a;
  --orange-text:#f0a020;
  --ink:#222;
  --body:#444;
  --nav:#4a4a4a;
  --nav-active:#333;
  --rule:#dcdcdc;
  --white:#fff;
  --sky:#5b97ad;
  --ground:#8a9aa0;
}
*{box-sizing:border-box;margin:0;padding:0}
html,body{width:725px;height:1200px;overflow:hidden;background:var(--white);font-family:'Open Sans',sans-serif;color:var(--body)}
.page{position:relative;width:725px;height:1200px}
.brand{position:absolute;display:flex;align-items:center;gap:11px}
.brand-mark{width:45px;height:45px;border-radius:6px;background:linear-gradient(var(--orange-light),var(--orange))}
.brand-name{font-size:21px;font-weight:600;color:var(--orange)}
.header-brand{left:82px;top:12px}
.auth{position:absolute;top:23px;right:82px;display:flex;gap:14px}
.auth a{display:block;width:58px;height:24px;line-height:22px;text-align:center;font-size:8px;font-weight:600;text-decoration:none;border:1px solid var(--orange)}
.btn-outline{color:var(--orange);background:var(--white)}
.btn-solid{color:var(--white);background:var(--orange)}
.nav{position:absolute;top:70px;left:0;width:725px;height:23px;background:var(--nav);display:flex;padding-left:79px}
.nav a{font-size:7px;font-weight:600;color:var(--white);text-decoration:none;line-height:23px;padding:0 13px;border-right:1px solid #5c5c5c}
.nav a.active{background:var(--nav-active)}
.nav a.wide{width:79px;text-align:center;padding:0}
.nav-search{position:absolute;right:95px;top:0;width:22px;height:23px;background:#111;display:flex;align-items:center;justify-content:center}
.hero{position:absolute;top:93px;left:0;width:725px;height:307px;background:linear-gradient(180deg,var(--sky) 0%,#6ea6b8 60%,#5aa04a 80%,var(--ground) 82%,var(--ground) 100%)}
.hero h1{position:absolute;left:81px;top:72px;font-size:26px;line-height:32px;font-weight:600;color:var(--white)}
.hero-dots{position:absolute;left:330px;top:275px;display:flex;gap:9px;align-items:center}
.hero-dots span{width:5px;height:5px;border-radius:50%;background:var(--white)}
.hero-dots span.on{width:7px;height:7px;background:none;border:1px solid var(--white)}
.section-title{color:var(--orange);font-weight:700;font-size:16px}
.services-title{position:absolute;top:436px;width:725px;text-align:center}
.services-intro{position:absolute;top:471px;width:725px;text-align:center;font-size:8.5px;line-height:15px}
.service{position:absolute;top:530px;width:120px;text-align:center}
.service svg{display:block;margin:0 auto;height:72px}
.service p{margin-top:20px;font-size:9.5px;font-weight:700;letter-spacing:3px;color:var(--ink)}
.rule{position:absolute;left:78px;width:569px;height:2px;background:var(--rule)}
.welcome-title{position:absolute;left:105px;top:718px}
.welcome-text{position:absolute;left:105px;top:754px;width:315px;font-size:8.5px;line-height:14.5px;color:var(--ink)}
.welcome-text p+p{margin-top:16px;color:var(--body)}
.read-more{position:absolute;left:106px;top:864px;width:83px;height:26px;border-radius:3px;background:linear-gradient(var(--orange-light),var(--orange));color:var(--white);font-size:8.5px;font-weight:700;display:flex;align-items:center;justify-content:center;gap:6px;text-decoration:none}
.welcome-badge{position:absolute;left:486px;top:756px;width:136px;height:136px;border-radius:9px;background:linear-gradient(var(--orange-light),var(--orange))}
.feature{position:absolute;top:974px;display:flex;gap:16px}
.feature-icon{width:54px;height:54px;border-radius:3px;background:linear-gradient(var(--orange-light),var(--orange));display:flex;align-items:center;justify-content:center}
.feature h3{font-size:9.5px;font-weight:600;color:var(--ink);line-height:14.5px}
.feature p{font-size:10px;color:var(--orange-text);line-height:16px;margin-top:4px}
.feature .phone{font-size:13px;margin-top:2px}
.footer-brand{left:82px;top:1114px}
.footer-menu{position:absolute;left:284px;top:1108px;font-size:7px;color:var(--body)}
.footer-menu h4,.footer-social h4{font-size:6.5px;font-weight:600;color:var(--ink);margin-bottom:16px}
.footer-menu nav{display:flex;gap:4px}
.footer-menu nav a{color:var(--body);text-decoration:none}
.footer-menu small{display:block;margin-top:9px;font-size:7px}
.footer-social{position:absolute;left:553px;top:1108px}
.footer-social div{display:flex;gap:9px}
.footer-social span{width:24px;height:24px;border:1px solid var(--orange);border-radius:3px}
</style>
</head>
<body>
<div class="page">
  <header>
    <div class="brand header-brand"><span class="brand-mark"></span><span class="brand-name">LoopVane</span></div>
    <div class="auth"><a class="btn-outline" href="#">SIGN UP</a><a class="btn-solid" href="#">SIGN IN</a></div>
  </header>
  <nav class="nav">
    <a class="active" href="#">HOME</a>
    <a class="wide" href="#">ABOUT US</a>
    <a class="wide" href="#">SERVICES</a>
    <a class="wide" href="#">FEATURES</a>
    <a href="#" style="padding:0 13px">CONTACT US</a>
    <span class="nav-search"><svg width="9" height="9" viewBox="0 0 10 10"><circle cx="4" cy="4" r="3" fill="none" stroke="#fff" stroke-width="1.5"/><line x1="6.2" y1="6.2" x2="9" y2="9" stroke="#fff" stroke-width="1.5"/></svg></span>
  </nav>
  <section class="hero" role="img" aria-label="Illustration of a yellow taxi in front of an airport terminal with a traveller using his phone">
    <h1>LOOPVANE offers<br><span style="font-weight:400">first world solutions</span></h1>
    <div class="hero-dots"><span></span><span class="on"></span><span></span><span></span><span></span></div>
  </section>
  <section>
    <h2 class="section-title services-title">OUR SERVICES</h2>
    <p class="services-intro">LOOPVANE is a heterogeneous ride-hailing service that<br>allows users for request transportation</p>
    <div class="service" style="left:123px">
      <svg viewBox="0 0 84 64" width="84"><path d="M18 4h48l10 22h6v26h-8v10h-10v-10H28v10H18v-10h-8V26h6z" fill="var(--orange)"/><path d="M22 10h40l7 16H15z" fill="#fff"/><circle cx="20" cy="38" r="5" fill="#fff"/><circle cx="64" cy="38" r="5" fill="#fff"/></svg>
      <p>TAXI</p>
    </div>
    <div class="service" style="left:302px">
      <svg viewBox="0 0 96 64" width="96"><rect x="46" y="2" width="34" height="4" fill="var(--orange)"/><rect x="61" y="4" width="4" height="10" fill="var(--orange)"/><path d="M2 10h6l8 12h30c6-8 34-10 38 10 2 12-6 20-20 20H50L36 32H12z" fill="var(--orange)"/><path d="M66 20c10 0 16 6 16 14H66z" fill="#fff"/><path d="M48 52v6h32M70 52v6M38 60h52" stroke="var(--orange)" stroke-width="3" fill="none"/></svg>
      <p>HELICOPTER</p>
    </div>
    <div class="service" style="left:480px">
      <svg viewBox="0 0 80 70" width="80"><path d="M40 0c4 0 6 6 6 14v12l32 6v10l-32-4v18l10 8v6l-16-4-16 4v-6l10-8V38L2 42V32l32-6V14c0-8 2-14 6-14z" fill="var(--orange)"/><g fill="#fff"><circle cx="22" cy="37" r="1.6"/><circle cx="28" cy="37" r="1.6"/><circle cx="16" cy="37" r="1.6"/><circle cx="52" cy="37" r="1.6"/><circle cx="58" cy="37" r="1.6"/><circle cx="64" cy="37" r="1.6"/></g></svg>
      <p>JET</p>
    </div>
  </section>
  <div class="rule" style="top:676px"></div>
  <section>
    <h2 class="section-title welcome-title">WELCOME TO OUR SITE</h2>
    <div class="welcome-text">
      <p>LOOPVANE offers first world solutions to first world problems. These days, our smartphones are our cameras, our wallets and our ride home.</p>
      <p>LOOPVANE guarantees that even if your phone is lost or dies, you'll never get stranded again. Simply call or text (SMS) our toll-free number to request a ride, and choose from one of the various services you subscribe to.</p>
    </div>
    <a class="read-more" href="#">READ MORE <svg width="4" height="6" viewBox="0 0 4 6"><path d="M0 0l4 3-4 3z" fill="#fff"/></svg></a>
    <div class="welcome-badge"></div>
  </section>
  <div class="rule" style="top:936px"></div>
  <section>
    <div class="feature" style="left:78px">
      <span class="feature-icon"><svg width="28" height="28" viewBox="0 0 28 28" fill="none" stroke="#222" stroke-width="2"><rect x="3" y="3" width="22" height="22" rx="3"/><path d="M14 20V8M9 13l5-5 5 5M9 7h10"/></svg></span>
      <div><h3>SIGN UP FOR FREE!</h3><p>Lorem Ipsum is simply<br>dummy text of the.</p></div>
    </div>
    <div class="feature" style="left:285px">
      <span class="feature-icon"><svg width="32" height="32" viewBox="0 0 32 32" fill="#222" stroke="#222" stroke-width="1.3"><path d="M16 6L6 12l4 12h12l4-12zM16 6v10M6 12l10 4 10-4M10 24l6-8 6 8" fill="none"/><circle cx="16" cy="6" r="2.5"/><circle cx="6" cy="12" r="2.5"/><circle cx="26" cy="12" r="2.5"/><circle cx="10" cy="24" r="2.5"/><circle cx="22" cy="24" r="2.5"/><circle cx="16" cy="16" r="3"/></svg></span>
      <div><h3>TRANSPORTATION<br>NETWORK</h3><p>Lorem Ipsum is simply</p></div>
    </div>
    <div class="feature" style="left:496px">
      <span class="feature-icon"><svg width="28" height="28" viewBox="0 0 28 28"><path d="M6 3l5 5-3 3c2 4 5 7 9 9l3-3 5 5-4 4C12 26 2 16 2 7z" fill="#222"/><path d="M16 6a6 6 0 016 6M16 2a10 10 0 0110 10" stroke="#222" stroke-width="1.8" fill="none"/></svg></span>
      <div style="padding-top:8px"><h3>CALL US NOW</h3><p class="phone">(555).555.0188</p></div>
    </div>
  </section>
  <div class="rule" style="top:1073px"></div>
  <footer>
    <div class="brand footer-brand"><span class="brand-mark"></span><span class="brand-name">LoopVane</span></div>
    <div class="footer-menu">
      <h4>MENU</h4>
      <nav><a href="#">Home</a>|<a href="#">About us</a>|<a href="#">Services</a>|<a href="#">Features</a> &nbsp;|<a href="#">Contact us</a></nav>
      <small>Copyrights @ 2017 All Rights Reserved</small>
    </div>
    <div class="footer-social">
      <h4>CONNECT WITH US</h4>
      <div><span></span><span></span><span></span></div>
    </div>
  </footer>
</div>
</body>
</html>
```